Veltrane Group Business Card Design

The CEO is looking for a new trendy look for his business card.
You can stay with current branding or come up with something new/creative. It can be 3D, including Medical Office buildings. You can use our logo in a variety of colors. Please include name, title, company name, company website, email address, cell number

Target Market(s)

Real Estate Development and Construction

Industry/Entity Type

Health care real estate

Contact Information for Business Card

Rohesh Kamdar, CEO M-604.781.2249 E-roheshkamdar@veltrane.com Address:4180 Lindqvist Ave, Tampa, FL 33482 www.veltrane.com

Font styles to use
Other font styles liked:
• Be creative

Requirements
Must have
• Creative, trendy look
Nice to have
• Please go to our website to get a feel- www. veltrane.com
Should not have
• small fonts

```html
<!DOCTYPE html>
<html lang="en">
<head>
<meta charset="utf-8">
<title>Veltrane Group Business Card</title>
<link rel="stylesheet" href="https://fonts.googleapis.com/css2?family=Poppins:wght@400;600;700&display=swap">
<style>
  :root {
    --brand-red: #b11e29;
    --brand-navy: #1c2b4a;
    --card-white: #ffffff;
    --backdrop: #e4e4e4;
  }
  * { margin: 0; padding: 0; box-sizing: border-box; }
  html, body { width: 1200px; height: 900px; overflow: hidden; }
  body {
    background: var(--backdrop);
    font-family: "Poppins", sans-serif;
    position: relative;
  }
  .card {
    position: absolute;
    top: 216px;
    width: 309px;
    height: 501px;
  }
  .card-front {
    left: 279px;
    background: var(--card-white);
    border-radius: 69px 0 69px 0;
  }
  .card-back {
    left: 623px;
    background: var(--brand-red);
    border-radius: 0 69px 0 69px;
  }
  .wordmark {
    position: absolute;
    text-align: right;
    font-weight: 700;
    line-height: 0.95;
    letter-spacing: -1px;
  }
  .wordmark .line-main { display: block; font-size: 46px; }
  .wordmark .line-sub { display: block; font-size: 28px; letter-spacing: 0; }
  .card-front .wordmark { right: 25px; top: 50px; color: var(--brand-red); }
  .card-back .wordmark { right: 48px; top: 336px; color: var(--card-white); }

  .name-marker {
    position: absolute;
    left: 0; top: 291px;
    width: 11px; height: 40px;
    background: var(--brand-red);
  }
  .identity { position: absolute; left: 32px; top: 293px; }
  .person-name {
    color: var(--brand-red);
    font-weight: 600;
    font-size: 19px;
    line-height: 1.1;
    letter-spacing: 0.3px;
  }
  .person-title {
    color: var(--brand-navy);
    font-weight: 600;
    font-size: 14px;
    line-height: 1.2;
  }
  .contact-list {
    position: absolute;
    left: 32px; top: 346px;
    list-style: none;
    color: var(--brand-navy);
    font-size: 15px;
    line-height: 18px;
  }
  .contact-list li { display: flex; align-items: center; gap: 5px; white-space: nowrap; }
  .contact-list svg { width: 13px; height: 13px; flex: none; }
  .address {
    position: absolute;
    left: 32px; top: 414px;
    color: var(--brand-navy);
    font-size: 15px;
    line-height: 18px;
    font-style: normal;
  }
</style>
</head>
<body>
  <section class="card card-front">
    <div class="wordmark"><span class="line-main">Veltrane</span><span class="line-sub">Group</span></div>
    <span class="name-marker"></span>
    <div class="identity">
      <p class="person-name">ROHESH KAMDAR</p>
      <p class="person-title">CEO</p>
    </div>
    <ul class="contact-list">
      <li>
        <svg viewBox="0 0 24 24" aria-hidden="true"><path fill="#b11e29" d="M6.6 10.8a15 15 0 0 0 6.6 6.6l2.2-2.2c.3-.3.7-.4 1-.2 1.1.4 2.300.6 3.6.6.6 0 1 .4 1 1V20c0 .6-.4 1-1 1A17 17 0 0 1 3 4c0-.6.4-1 1-1h3.5c.6 0 1 .4 1 1 0 1.3.2 2.5.6 3.6.1.3 0 .7-.2 1z"/></svg>
        604.781.2249
      </li>
      <li>
        <svg viewBox="0 0 24 24" aria-hidden="true"><rect x="2" y="5" width="20" height="14" fill="#b11e29"/><path d="M2 5l10 8 10-8M2 19l8-7M22 19l-8-7" fill="none" stroke="#fff" stroke-width="1.6"/></svg>
        roheshkamdar@veltrane.com
      </li>
      <li>
        <svg viewBox="0 0 24 24" aria-hidden="true"><g fill="none" stroke="#b11e29" stroke-width="2"><circle cx="12" cy="12" r="9.5"/><ellipse cx="12" cy="12" rx="4" ry="9.5"/><path d="M2.5 12h19M4 7h16M4 17h16"/></g></svg>
        www.veltrane.com
      </li>
    </ul>
    <address class="address">4180 Lindqvist<br>Ave, Tampa<br>FL 33482</address>
  </section>

  <section class="card card-back">
    <div class="wordmark"><span class="line-main">Veltrane</span><span class="line-sub">Group</span></div>
  </section>
</body>
</html>
```